Meridale Staffing Website

My business has been word of mouth over the last 3 years and has grown. Now I need a website for additional marketing as we have new clients asking for a website.

You have already completed my Logo during an earlier project. I have attached the logo.

We do Staff Augmentation and Operation Support.

What is that?
Staff augmentation is an outsourcing strategy that allows companies to fill specific, temporary roles to achieve business objectives. This staffing method complements existing teams with specific talent, enhancing business capabilities or filling gaps left by members on extended leave.

We work alongside the internal recruiting team to assist clients to meet and exceed financial goals.

```html
<!DOCTYPE html>
<html lang="en">
<head>
<meta charset="utf-8">
<title>Meridale Staffing</title>
<link href="https://fonts.googleapis.com/css2?family=Lato:wght@400;700&family=Rubik:wght@400;500;700&display=swap" rel="stylesheet">
<style>
:root{
  --navy:#0e3f6e;
  --navy-dark:#0b355f;
  --blue:#1d5fa8;
  --teal:#2a6a8e;
  --ink:#1c1c1c;
  --text:#3b3b3b;
  --white:#ffffff;
  --line:#d8dde3;
}
*{margin:0;padding:0;box-sizing:border-box}
html,body{width:1200px;height:3546px;overflow:hidden;background:var(--white)}
body{position:relative;font-family:"Lato",sans-serif;color:var(--text)}
.abs{position:absolute}
.heading{font-family:"Rubik",sans-serif;font-weight:700;color:var(--ink);letter-spacing:.3px}
.sub{font-family:"Rubik",sans-serif;font-weight:400;color:var(--blue);font-size:19px;letter-spacing:.4px}

/* top bar */
.topbar{left:0;top:0;width:1200px;height:39px;background:var(--navy);color:var(--white);font-size:15px}
.topbar .item{position:absolute;top:7px;display:flex;align-items:center;gap:10px}
.ring{width:24px;height:24px;border:1.5px solid var(--white);border-radius:50%;display:inline-block}
.socials{position:absolute;top:7px;left:958px;display:flex;gap:8px}
.logo-tab{left:91px;top:6px;width:230px;height:82px;background:var(--white);border-radius:14px 14px 0 0}
.brand{display:flex;align-items:center;gap:10px;font-family:"Rubik",sans-serif;font-weight:500;color:var(--navy);font-size:23px;line-height:1.05}
.brand .mark{width:40px;height:40px;border-radius:50%;background:var(--navy)}
.nav{left:509px;top:56px;display:flex;gap:55px;font-family:"Rubik",sans-serif;font-size:15px;color:var(--ink)}
.nav .active{border-bottom:2px solid var(--navy);padding-bottom:6px}

/* hero */
.hero{left:0;top:94px;width:1200px;height:598px;background:linear-gradient(100deg,#dfe6ec 0%,#cfd6dc 35%,#b9a99a 60%,#3a3a3c 100%)}
.hero-badge{left:59px;top:247px;width:372px;height:372px;border-radius:50%;background:rgba(31,96,132,.92);border:4px solid var(--white)}
.hero-title{left:111px;top:328px;color:var(--white);font-family:"Rubik",sans-serif;font-weight:500;font-size:52px;line-height:54px}
.hero-sub{left:113px;top:451px;color:var(--white);font-family:"Rubik",sans-serif;font-size:19px}
.pill{display:flex;align-items:center;justify-content:space-between;border-radius:30px;font-family:"Rubik",sans-serif;font-weight:500;color:var(--ink)}
.pill .dot{width:28px;height:28px;border-radius:50%;border:3px solid var(--navy)}
.hero-btn{left:114px;top:495px;width:199px;height:46px;background:var(--white);padding:0 14px 0 23px;font-size:14px}
.dots{left:560px;top:638px;display:flex;gap:10px}
.dots span{width:12px;height:12px;border-radius:50%;background:rgba(255,255,255,.6)}
.dots span:first-child{background:var(--white)}

/* about */
.about-media{left:110px;top:782px;width:543px;height:360px;background:linear-gradient(110deg,#5b6066 0%,#9aa4ae 45%,#cbd2d8 70%,#6f7e8c 100%)}
.play{left:349px;top:930px;width:66px;height:66px;border:3px solid var(--white);border-radius:50%}
.about-title{left:707px;top:797px;font-size:30px}
.about-sub{left:707px;top:847px}
.about-text{left:707px;top:890px;width:375px;font-size:15px;line-height:25.7px;color:var(--text)}
.about-btn{left:704px;top:1069px;width:208px;height:49px;border:2px solid var(--navy);padding:0 18px 0 28px;font-size:15px;background:var(--white)}

/* services */
.svc-title{left:109px;top:1234px;font-size:30px}
.svc-sub{left:109px;top:1285px}
.card{top:1342px;height:565px;overflow:hidden}
.card .label{position:absolute;left:36px;color:var(--white)}
.card h3{font-family:"Rubik",sans-serif;font-weight:700;font-size:26px;line-height:36px;letter-spacing:.3px}
.card p{font-size:15px;line-height:26px;margin-top:10px}
.card svg{display:block;margin-top:18px}

/* team */
.team-title{left:0;top:1990px;width:1200px;text-align:center;font-size:30px}
.team-sub{left:0;top:2041px;width:1200px;text-align:center}
.portrait{border-radius:50%}
.quote-text{left:690px;top:2190px;width:398px;text-align:right;font-size:15px;line-height:25.7px}
.quote-name{left:690px;top:2320px;width:398px;text-align:right;font-size:14px}
.quote-name b{font-family:"Rubik",sans-serif;font-weight:500;font-size:18px;color:var(--ink);margin-right:14px}
.qbtn{top:2380px;width:96px;height:38px;border-radius:20px;background:var(--white);box-shadow:0 3px 10px rgba(0,0,0,.15);display:flex;align-items:center;justify-content:center}

/* clients */
.clients{left:0;top:2550px;width:1200px;height:329px;background:var(--navy)}
.clients-title{left:0;top:2588px;width:1200px;text-align:center;font-size:30px;color:var(--white)}
.clients-sub{left:0;top:2640px;width:1200px;text-align:center;color:var(--white)}
.carrow{top:2733px;width:44px;height:44px;border-radius:50%;background:var(--white);display:flex;align-items:center;justify-content:center}
.client{top:2710px;width:200px;display:flex;flex-direction:column;align-items:center;gap:10px;color:var(--white);font-family:"Rubik",sans-serif;font-size:22px;font-weight:500}
.client .shape{width:52px;height:52px;border-radius:50%;border:3px solid var(--white)}

/* newsletter */
.news{left:0;top:2879px;width:1200px;height:311px;background:linear-gradient(90deg,#d9dde2 0%,#e9ecef 40%,#eef0f2 100%)}
.news-title{left:0;top:2957px;width:1200px;text-align:center;font-size:30px}
.news-sub{left:0;top:3008px;width:1200px;text-align:center}
.news-form{left:341px;top:3048px;width:514px;height:58px;background:var(--white);border:1px solid var(--line);border-radius:30px;display:flex;align-items:center;padding-left:24px}
.news-form span{margin-left:24px;font-size:15px;color:#9a9a9a}
.signup{left:717px;top:3051px;width:136px;height:52px;border-radius:26px;background:var(--navy);color:var(--white);font-family:"Rubik",sans-serif;font-weight:500;font-size:15px;display:flex;align-items:center;justify-content:center}

/* footer */
.footer{left:0;top:3190px;width:1200px;height:356px;background:var(--navy);color:var(--white)}
.fbrand{left:113px;top:3268px;color:var(--white)}
.fbrand .mark{background:var(--white)}
.fsocial{left:111px;top:3354px;display:flex;gap:14px}
.fsocial .ring{width:30px;height:30px;border-width:2px}
.fcol{top:3270px;color:var(--white)}
.fcol h4{font-family:"Rubik",sans-serif;font-weight:400;font-size:21px;margin-bottom:14px}
.fcol li{list-style:none;font-size:15px;line-height:25.5px}
.contact-row{display:flex;gap:14px;font-size:15px;line-height:23px;margin-bottom:14px}
.divider{left:110px;top:3469px;width:995px;height:1px;background:rgba(255,255,255,.5)}
.copy{left:0;top:3501px;width:1200px;text-align:center;font-size:15px;color:var(--white)}
</style>
</head>
<body>

<!-- top bar -->
<div class="abs topbar">
  <div class="item" style="left:362px">
    <svg width="26" height="26" viewBox="0 0 26 26"><circle cx="13" cy="13" r="11.5" fill="none" stroke="#fff" stroke-width="1.5"/><path d="M9 7.5c1 0 1.5 2.5 1 3s-1 .7-.4 1.8 2 2.5 3 3 1.2-.2 1.8-.6 3 .3 3 1.3-1.2 2-2.5 2-4.5-1.5-6.3-3.6S7.5 10 7.8 8.8 8.5 7.5 9 7.5z" fill="#fff"/></svg>
    +1(555)-014-2290
  </div>
  <div class="item" style="left:627px">
    <svg width="26" height="26" viewBox="0 0 26 26"><circle cx="13" cy="13" r="11.5" fill="none" stroke="#fff" stroke-width="1.5"/><rect x="7" y="9" width="12" height="8" fill="#fff"/><path d="M7 9l6 4.5L19 9" fill="none" stroke="#0e3f6e" stroke-width="1.2"/></svg>
    info@meridalestaffing.com
  </div>
  <div class="socials"><span class="ring"></span><span class="ring"></span><span class="ring"></span><span class="ring"></span></div>
</div>

<!-- header -->
<div class="abs logo-tab"></div>
<div class="abs brand" style="left:110px;top:18px"><span class="mark"></span><span>MERIDALE<br><small style="font-size:15px">STAFFING</small></span></div>
<nav class="abs nav">
  <span class="active">HOME</span><span>ABOUT</span><span>SERVICE</span><span>TEAM</span><span>NEWS</span><span>CONTACT</span>
</nav>

<!-- hero -->
<div class="abs hero" role="img" aria-label="Photo of a smiling businesswoman interviewing a candidate across a desk"></div>
<div class="abs hero-badge"></div>
<div class="abs hero-title">MERIDALE<br>STAFFING</div>
<div class="abs hero-sub">DOLORIBUS ASPERIORES</div>
<div class="abs pill hero-btn">GET STARTED <span class="dot"></span></div>
<div class="abs dots"><span></span><span></span><span></span><span></span></div>

<!-- about -->
<div class="abs about-media" role="img" aria-label="Video still of a recruiter talking with a smiling candidate in an office"></div>
<div class="abs play"><svg width="60" height="60" viewBox="0 0 60 60"><path d="M24 19 L42 30 L24 41 Z" fill="#fff"/></svg></div>
<h2 class="abs heading about-title">ABOUT US</h2>
<div class="abs sub about-sub">PERFERENDIS DOLORIBUS ASPERIORES</div>
<p class="abs about-text">Eligendi Optio Cumque Nihil Impedit Quo Minus Id Quod Maxime Placeat Facere Possimus, Omnis Voluptas Assumenda Est, Omnis Dolor Repellendus. Temporibus Autem Quibusdam Et Aut Officiis Debitis Aut Rerum Necessitatibus Saepe Eveniet Ut Et Voluptates Repudiandae Sint Et Molestiae Non</p>
<div class="abs pill about-btn">READ MORE <span class="dot"></span></div>

<!-- services -->
<h2 class="abs heading svc-title">OUR SERVICES</h2>
<div class="abs sub svc-sub">PERFERENDIS DOLORIBUS ASPERIORES</div>
<svg class="abs" style="left:985px;top:1283px" width="104" height="20" viewBox="0 0 104 20">
  <path d="M46 10H2M10 3L2 10l8 7" fill="none" stroke="#c9cdd2" stroke-width="2.5"/>
  <path d="M58 10h44M94 3l8 7-8 7" fill="none" stroke="#111" stroke-width="2.5"/>
</svg>

<div class="abs card" style="left:0;width:380px;background:linear-gradient(180deg,#b9bcc0 0%,#7d7a78 55%,#1e1e1e 100%)" role="img" aria-label="Photo of a smiling consultant in a blazer beside a whiteboard">
  <div class="label" style="top:438px"><h3>STAFF AUGMENTATION</h3>
    <svg width="34" height="28" viewBox="0 0 34 28"><path d="M2 14h28M18 3l12 11-12 11" fill="none" stroke="#fff" stroke-width="4"/></svg></div>
</div>
<div class="abs card" style="left:403px;width:391px;background:linear-gradient(180deg,#c8cbcf 0%,#6d6c6b 50%,#161616 100%)" role="img" aria-label="Photo of colleagues reviewing documents at a meeting table">
  <div class="label" style="top:327px;left:41px"><h3>BEHAVIORAL<br>DEVELOPMENT</h3>
    <p>Et Aut Officiis Debitis Aut Rerum<br>Necessitatibus Saepe Eveniet Ut Et<br>Voluptates Repudiandae Sint Et</p>
    <svg width="34" height="28" viewBox="0 0 34 28"><path d="M2 14h28M18 3l12 11-12 11" fill="none" stroke="#fff" stroke-width="4"/></svg></div>
</div>
<div class="abs card" style="left:816px;width:384px;background:linear-gradient(180deg,#d7c6b8 0%,#3f5a52 55%,#1a1c1b 100%)" role="img" aria-label="Photo of a smiling woman with glasses in a team meeting">
  <div class="label" style="top:440px;left:42px"><h3>OPERATION SUPPORT</h3>
    <svg width="34" height="28" viewBox="0 0 34 28"><path d="M2 14h28M18 3l12 11-12 11" fill="none" stroke="#fff" stroke-width="4"/></svg></div>
</div>

<!-- team -->
<h2 class="abs heading team-title">OUR TEAM</h2>
<div class="abs sub team-sub">PERFERENDIS DOLORIBUS ASPERIORES</div>
<div class="abs portrait" style="left:101px;top:2163px;width:96px;height:96px;background:radial-gradient(circle,#b08d75,#4b4f56)" role="img" aria-label="Team member portrait"></div>
<div class="abs portrait" style="left:-8px;top:2333px;width:126px;height:126px;background:radial-gradient(circle,#b88f74,#5a7fa6)" role="img" aria-label="Team member portrait"></div>
<div class="abs portrait" style="left:201px;top:2387px;width:76px;height:76px;background:radial-gradient(circle,#c9957a,#5b4b43)" role="img" aria-label="Team member portrait"></div>
<div class="abs portrait" style="left:268px;top:2097px;width:347px;height:347px;background:radial-gradient(circle at 50% 45%,#c79a80 0%,#6c4f3f 45%,#1d1d1f 100%)" role="img" aria-label="Portrait of the featured team member"></div>
<svg class="abs" style="left:1045px;top:2140px" width="44" height="38" viewBox="0 0 44 38">
  <circle cx="10" cy="10" r="9" fill="#1d4f8c"/><path d="M19 10c0 12-6 22-16 26l-2-4c6-3 10-9 10-14z" fill="#1d4f8c"/>
  <circle cx="32" cy="10" r="9" fill="#1d4f8c"/><path d="M41 10c0 12-6 22-16 26l-2-4c6-3 10-9 10-14z" fill="#1d4f8c"/>
</svg>
<p class="abs quote-text">Eligendi Optio Cumque Nihil Impedit Quo Minus Id Quod Maxime Placeat Facere Possimus, Omnis Voluptas Assumenda Est, Omnis Dolor Repellendus. Temporibus Autem Quibusdam Et Aut Officiis Debitis Aut Rerum</p>
<div class="abs quote-name"><b>Dana Hollis</b>Doloribus Asperiores Repellat</div>
<div class="abs qbtn" style="left:889px"><svg width="28" height="18" viewBox="0 0 28 18"><path d="M26 9H3M10 2L3 9l7 7" fill="none" stroke="#111" stroke-width="3"/></svg></div>
<div class="abs qbtn" style="left:992px"><svg width="28" height="18" viewBox="0 0 28 18"><path d="M2 9h23M18 2l7 7-7 7" fill="none" stroke="#555" stroke-width="2.5"/></svg></div>

<!-- clients -->
<div class="abs clients"></div>
<h2 class="abs heading clients-title">OUR CLIENTS</h2>
<div class="abs sub clients-sub">PERFERENDIS DOLORIBUS ASPERIORES</div>
<div class="abs carrow" style="left:34px"><svg width="16" height="16" viewBox="0 0 16 16"><path d="M10 2L4 8l6 6" fill="none" stroke="#0e3f6e" stroke-width="3"/></svg></div>
<div class="abs carrow" style="left:1119px"><svg width="16" height="16" viewBox="0 0 16 16"><path d="M6 2l6 6-6 6" fill="none" stroke="#0e3f6e" stroke-width="3"/></svg></div>
<div class="abs client" style="left:124px"><span class="shape"></span>Brightcrew</div>
<div class="abs client" style="left:372px"><span class="shape"></span>Teamhaven</div>
<div class="abs client" style="left:622px"><span class="shape"></span>Cloudhire</div>
<div class="abs client" style="left:874px"><span class="shape"></span>Seekwell</div>

<!-- newsletter -->
<div class="abs news" role="img" aria-label="Faded photo of a smiling woman with glasses"></div>
<h2 class="abs heading news-title">SUBSCRIBE TO OUR NEWSLETTER</h2>
<div class="abs sub news-sub">PERFERENDIS DOLORIBUS ASPERIORES</div>
<div class="abs news-form">
  <svg width="28" height="20" viewBox="0 0 28 20"><rect x="1" y="1" width="26" height="18" fill="none" stroke="#333" stroke-width="1.8"/><path d="M1 1l13 10L27 1M1 19l9-8M27 19l-9-8" fill="none" stroke="#333" stroke-width="1.8"/></svg>
  <span>Enter your Email address</span>
</div>
<div class="abs signup">SIGN UP</div>

<!-- footer -->
<div class="abs footer"></div>
<div class="abs brand fbrand"><span class="mark"></span><span style="color:#fff;font-size:28px">MERIDALE<br><small style="font-size:18px">STAFFING</small></span></div>
<div class="abs fsocial"><span class="ring"></span><span class="ring"></span><span class="ring"></span><span class="ring"></span></div>
<div class="abs fcol" style="left:403px"><h4>QUICK LINKS</h4><ul><li>Home</li><li>About</li><li>Service</li><li>Team</li><li>Contact</li></ul></div>
<div class="abs fcol" style="left:619px"><h4>SERVICES</h4><ul><li>Staff Augmentation</li><li>Operation Support</li><li>Behavioral Development</li></ul></div>
<div class="abs fcol" style="left:885px">
  <h4>CONTACT US</h4>
  <div class="contact-row"><svg width="20" height="24" viewBox="0 0 20 24"><path d="M10 1a8 8 0 0 0-8 8c0 6 8 14 8 14s8-8 8-14a8 8 0 0 0-8-8z" fill="#fff"/><circle cx="10" cy="9" r="3" fill="#0e3f6e"/></svg><span>Quod Maxime Placeat<br>Facere Possimus, Omnis</span></div>
  <div class="contact-row"><svg width="20" height="20" viewBox="0 0 20 20"><path d="M4 1c1.5 0 2.5 4 2 5s-1.5 1 -.5 3 3 4 5 5 1.5 0 3-1 5 .5 5 2-2 4-4 4S7 17 4.5 14 1 6 1.5 4 3 1 4 1z" fill="#fff"/></svg><span>+1(555)-014-2290</span></div>
  <div class="contact-row"><svg width="20" height="16" viewBox="0 0 20 16"><rect x="0" y="1" width="20" height="14" fill="#fff"/><path d="M0 1l10 7 10-7" fill="none" stroke="#0e3f6e" stroke-width="1.5"/></svg><span>info@meridalestaffing.com</span></div>
</div>
<div class="abs divider"></div>
<div class="abs copy">CopyRights @2022 Meridale Staffing. All Rights Reserved.</div>

</body>
</html>
```